Where the Lantern Fades: A Sacred Wandering

This is a memoir about my breakdown/breakthrough followed by a spiritual awakening in 2012, I found my guru Harsh Omveli Dev, Mother Ayahuasca, and my spiritual mother, Ishu. By 2013, I was headed for a spiritual adventure through India, Southeast India, and Nepal which lasted 14 months. I lived in ashrams, meditated and prayed in temples,, traveled by train and bus, met many enlightened beings and interesting people. During Vipassana, I discovered my true essence- the light of my soul. It is a book of travel, romance, and spiritual growth. My idea is a road lined with temples, etc. I am walking down the road and see myself at the end of the road, facing out, with a bright star in my heart center. I see the colors in muted yellows and other earth-tone hues. Marigolds are used everywhere in the temples to adorn statues and doorways and this speaks to me. The title of the book is about finding out who I am beyond my stories and it is also about how our story will reveal to us who we really are.

Target Market(s)

Spiritual seekers, adventurers, travelers

Industry/Entity Type

Spiritual

Font styles to use
Serif
Sans Serif
Other font styles liked:
• I’m open. I like simplicity

Colors
FFC000
F8CF3A
FAE287
FDF2CF
FEFAEE

Requirements
Must have
• My name: Carla Serena Tovi, Earth tones, pastels, me or a likeness of me, room for ISBN on back cover
Nice to have
• In the photo uploads I drew an idea of what I would like, there is also the idea in the book
Should not have
• I am not a fan of bright colors and that's all I can select here. I like neutral colors, like browns, slate, creams, and whites. This reflects the dusty roads I took throughout my journey.

```html
<!DOCTYPE html>
<html lang="en">
<head>
<meta charset="utf-8">
<title>Where the Lantern Fades — Cover</title>
<link rel="stylesheet" href="https://fonts.googleapis.com/css2?family=Marcellus&family=Cormorant+Garamond:ital,wght@1,500&display=swap">
<style>
  :root {
    --backdrop: #262626;
    --sky-top: #b9462a;
    --sky-upper: #d9692c;
    --sky-mid: #f29a36;
    --glow: #f8c848;
    --shore: #f2b63c;
    --sand-deep: #cf7a24;
    --sun-core: #fffbe6;
    --title-ink: #ffffff;
    --subtitle-ink: #1a1208;
  }
  * { margin: 0; padding: 0; box-sizing: border-box; }
  html, body {
    width: 1200px;
    height: 1200px;
    overflow: hidden;
    background: var(--backdrop);
  }
  .canvas {
    position: relative;
    width: 1200px;
    height: 1200px;
  }
  .cover {
    position: absolute;
    left: 218px;
    top: 27px;
    width: 764px;
    height: 1147px;
    overflow: hidden;
  }
  .cover-art {
    position: absolute;
    inset: 0;
    background:
      radial-gradient(circle at 84% 71%, var(--sun-core) 0%, rgba(255,240,170,0.85) 5%, rgba(250,210,90,0.45) 16%, rgba(250,200,80,0) 34%),
      linear-gradient(180deg,
        var(--sky-top) 0%,
        var(--sky-upper) 18%,
        var(--sky-mid) 40%,
        var(--glow) 62%,
        var(--shore) 78%,
        var(--sand-deep) 100%);
  }
  .title {
    position: absolute;
    left: 0;
    right: 0;
    top: 86px;
    text-align: center;
    font-family: "Marcellus", serif;
    font-weight: 400;
    font-size: 122px;
    line-height: 159px;
    letter-spacing: 4px;
    color: var(--title-ink);
  }
  .title span { display: block; }
  .subtitle {
    position: absolute;
    left: 0;
    right: 0;
    top: 758px;
    text-align: center;
    font-family: "Cormorant Garamond", serif;
    font-style: italic;
    font-weight: 500;
    font-size: 56px;
    letter-spacing: 5px;
    color: var(--subtitle-ink);
  }
  .author {
    position: absolute;
    left: 0;
    right: 0;
    top: 1072px;
    text-align: center;
    font-family: "Marcellus", serif;
    font-size: 26px;
    letter-spacing: 3px;
    color: var(--title-ink);
  }
</style>
</head>
<body>
  <main class="canvas">
    <section class="cover">
      <div class="cover-art" role="img" aria-label="Glowing golden sunset sky over a misty shoreline, with a lone cloaked woman walking toward a bright sun"></div>
      <h1 class="title">
        <span>WHERE</span>
        <span>THE</span>
        <span>LANTERN</span>
        <span>FADES</span>
      </h1>
      <p class="subtitle">A Sacred Wandering</p>
      <p class="author">CARLA SERENA TOVI</p>
    </section>
  </main>
</body>
</html>
```